Redesign of business card for Cedar Ridge Mechanical

We are looking for a new design for our business cards for Cedar Ridge Mechanical. We are a plumbing & HVAC construction company, operating on the West Coast of Canada and USA. Logo attached.
Industry/Entity Type
Construction - Plumbing & HVAC
Contact Information for Business Card
Name, address, phone numbers, email, website address
Look and feel
Each slider illustrates characteristics of the customer's brand and the style your logo design should communicate.

```html
<!DOCTYPE html>
<html lang="en">
<head>
<meta charset="utf-8">
<title>Cedar Ridge Mechanical – Business Card</title>
<link href="https://fonts.googleapis.com/css2?family=Montserrat:wght@400;500;700&display=swap" rel="stylesheet">
<style>
  :root {
    --stage: #161616;
    --card-front: #ffffff;
    --card-back: #1f1f1f;
    --ink: #111111;
    --ink-soft: #7a7a7a;
    --rule: #9a9a9a;
    --back-text: #8a8a8a;
  }
  * { margin: 0; padding: 0; box-sizing: border-box; }
  html, body {
    width: 1200px; height: 963px; overflow: hidden;
    background: var(--stage);
    font-family: "Montserrat", sans-serif;
  }
  .stage {
    width: 1200px; height: 963px;
    display: flex; flex-direction: column; align-items: center; justify-content: center;
    gap: 40px;
  }
  .card {
    width: 700px; height: 400px;
    border-radius: 4px;
    box-shadow: 0 10px 30px rgba(0,0,0,.5);
  }
  .card-front {
    background: var(--card-front);
    display: flex; align-items: center;
    padding: 0 50px;
  }
  .brand {
    width: 290px;
    display: flex; align-items: center; gap: 14px;
  }
  .brand-square {
    width: 34px; height: 34px; flex: none;
    background: var(--ink);
  }
  .brand-name {
    font-weight: 700; font-size: 20px; line-height: 1.2;
    letter-spacing: .5px; text-transform: uppercase;
    color: var(--ink);
  }
  .divider {
    width: 1px; height: 190px;
    background: var(--rule);
    margin: 0 34px 0 16px;
  }
  .details { color: var(--ink-soft); }
  .person-name {
    font-weight: 700; font-size: 24px; letter-spacing: 1px;
    text-transform: uppercase; color: var(--ink);
  }
  .person-name .surname { color: var(--ink-soft); }
  .person-role { font-size: 15px; color: var(--ink); margin-bottom: 12px; }
  .address { font-size: 17px; line-height: 1.3; margin-bottom: 12px; }
  .contact-list { list-style: none; font-size: 17px; line-height: 1.5; }
  .contact-list li { display: flex; align-items: center; gap: 8px; }
  .contact-list svg { width: 14px; height: 14px; fill: var(--ink); flex: none; }
  .contact-list .web { color: var(--ink); }
  .card-back {
    background: var(--card-back);
    display: flex; align-items: center; justify-content: center; gap: 18px;
  }
  .card-back .brand-square { background: var(--back-text); width: 40px; height: 40px; }
  .card-back .brand-name { color: var(--back-text); font-size: 30px; }
</style>
</head>
<body>
<main class="stage">
  <section class="card card-front">
    <div class="brand">
      <span class="brand-square"></span>
      <span class="brand-name">Cedar Ridge Mechanical</span>
    </div>
    <div class="divider"></div>
    <div class="details">
      <h1 class="person-name">Daniel <span class="surname">Harper</span></h1>
      <p class="person-role">Manager</p>
      <p class="address">Your address, city<br>state, ZIP 0000</p>
      <ul class="contact-list">
        <li>
          <svg viewBox="0 0 24 24" aria-hidden="true"><path d="M6.6 10.8a15.1 15.1 0 0 0 6.6 6.6l2.2-2.2c.3-.3.7-.4 1-.2 1.1.4 2.3.6 3.6.6.6 0 1 .4 1 1V20c0 .6-.4 1-1 1C10.6 21 3 13.4 3 4c0-.6.4-1 1-1h3.5c.6 0 1 .4 1 1 0 1.3.2 2.5.6 3.6.1.3 0 .7-.2 1L6.6 10.8z"/></svg>
          123-456-2100
        </li>
        <li>
          <svg viewBox="0 0 24 24" aria-hidden="true"><path d="M2 5h20v14H2V5zm2 2v.5l8 5 8-5V7H4zm0 2.8V17h16V9.8l-8 5-8-5z"/></svg>
          youremail@mailbox.com
        </li>
        <li>
          <svg viewBox="0 0 24 24" aria-hidden="true"><circle cx="12" cy="12" r="10"/></svg>
          <span class="web">www.yourwebsite.com</span>
        </li>
      </ul>
    </div>
  </section>

  <section class="card card-back">
    <span class="brand-square"></span>
    <span class="brand-name">Cedar Ridge Mechanical</span>
  </section>
</main>
</body>
</html>
```